Irrigation Business needs their business cards modernised and revamped

I would like to keep my current logo, colours and revamp the format of the card.

I would like the card to be clean yet important.

Im not sure if you include texture but i would like the named logo to be indented into the card etc.

show me something alive and free something thats clinical to the point yet has a feel of achievement. i would like people to go nice card.

Target Market(s)

high end clients, corporate, sports field manger, the guys that make the decisions

Industry/Entity Type

Business

Contact Information for Business Card

nformation to be included

Dean Harlow (Director)
0487305526
dean@kolvat.biz
www.kestonfieldworks.com

instagram logo
google logo
facebook logo

Colors

Designer to choose colors to be used in the design.

Requirements
Nice to have
• indentations a really nice feel to the card good texture

```html
<!DOCTYPE html>
<html lang="en">
<head>
<meta charset="utf-8">
<title>Keston Fieldworks – Business Card</title>
<link rel="stylesheet" href="https://fonts.googleapis.com/css2?family=Open+Sans:wght@400;700;800&display=swap">
<style>
  :root {
    --brand-blue: #2f6aae;
    --sky-blue: #33a6d8;
    --ink-grey: #555a60;
    --card-white: #ffffff;
    --backdrop: #e9e6e1;
  }
  * { margin: 0; padding: 0; box-sizing: border-box; }
  html, body {
    width: 1200px;
    height: 900px;
    overflow: hidden;
    background: var(--backdrop);
    font-family: "Open Sans", Arial, sans-serif;
  }
  .canvas {
    position: relative;
    width: 1200px;
    height: 900px;
  }
  .card {
    position: absolute;
    left: 250px;
    width: 700px;
    height: 400px;
    overflow: hidden;
    box-shadow: 0 6px 18px rgba(0,0,0,0.18);
  }
  .card-back { top: 30px; background: var(--brand-blue); }
  .card-front { top: 470px; background: var(--card-white); }

  /* back */
  .back-mark {
    position: absolute;
    inset: 0;
    display: flex;
    flex-direction: column;
    align-items: center;
    justify-content: center;
    gap: 22px;
  }
  .back-mark .mark-circle {
    width: 110px; height: 110px;
    border-radius: 50%;
    background: var(--card-white);
  }
  .back-mark .mark-name {
    color: var(--card-white);
    font-weight: 800;
    font-size: 30px;
    letter-spacing: 1px;
  }

  /* front */
  .wave { position: absolute; left: 0; top: 0; width: 700px; height: 400px; }
  .person { position: absolute; left: 62px; top: 78px; }
  .person-name {
    font-weight: 700;
    font-size: 24px;
    color: var(--brand-blue);
    letter-spacing: 0.3px;
  }
  .person-name .surname { color: var(--sky-blue); }
  .person-role { font-size: 16px; color: var(--ink-grey); margin-top: -2px; }

  .brand {
    position: absolute;
    right: 40px;
    top: 52px;
    display: flex;
    flex-direction: column;
    align-items: center;
    gap: 10px;
  }
  .brand-circle {
    width: 78px; height: 78px;
    border-radius: 50%;
    background: var(--brand-blue);
  }
  .brand-name {
    font-weight: 800;
    font-size: 30px;
    color: var(--brand-blue);
    letter-spacing: -0.5px;
  }

  .contacts {
    position: absolute;
    left: 62px;
    top: 236px;
    list-style: none;
  }
  .contacts li {
    display: flex;
    align-items: center;
    gap: 8px;
    font-size: 18px;
    color: var(--ink-grey);
    line-height: 27px;
  }
  .contact-icon {
    width: 20px; height: 20px;
    flex: none;
  }

  .social {
    position: absolute;
    right: 30px;
    top: 220px;
    display: flex;
    gap: 8px;
  }
  .social span {
    width: 26px; height: 26px;
    border-radius: 50%;
    background: var(--card-white);
    opacity: 0.9;
  }
</style>
</head>
<body>
<main class="canvas">

  <section class="card card-back" aria-label="Card back">
    <div class="back-mark">
      <div class="mark-circle"></div>
      <div class="mark-name">KESTON FIELDWORKS</div>
    </div>
  </section>

  <section class="card card-front" aria-label="Card front">
    <svg class="wave" viewBox="0 0 700 400" aria-hidden="true">
      <path d="M0 400 L0 330 C 160 360 300 330 420 250 C 500 195 580 175 700 168 L700 400 Z" fill="var(--sky-blue)"/>
      <path d="M0 400 L0 345 C 180 372 320 345 440 262 C 520 208 600 185 700 178 L700 400 Z" fill="var(--card-white)"/>
      <path d="M0 400 L0 352 C 190 378 330 355 452 272 C 530 220 610 195 700 188 L700 400 Z" fill="var(--brand-blue)"/>
    </svg>

    <div class="person">
      <div class="person-name">DEAN <span class="surname">HARLOW</span></div>
      <div class="person-role">Director</div>
    </div>

    <div class="brand">
      <div class="brand-circle"></div>
      <div class="brand-name">KESTON FIELDWORKS</div>
    </div>

    <ul class="contacts">
      <li>
        <svg class="contact-icon" viewBox="0 0 20 20" aria-hidden="true">
          <circle cx="10" cy="10" r="10" fill="var(--brand-blue)"/>
          <path d="M6 7 Q6 5 8 5 L8.5 7.5 L7.5 8.3 Q8.5 11 11.7 12.5 L12.5 11.5 L15 12 Q15 14 13 14 Q7 13 6 7 Z" fill="#fff"/>
        </svg>
        0487305526
      </li>
      <li>
        <svg class="contact-icon" viewBox="0 0 20 20" aria-hidden="true">
          <circle cx="10" cy="10" r="10" fill="var(--brand-blue)"/>
          <rect x="5" y="6.5" width="10" height="7" fill="#fff"/>
          <path d="M5 6.5 L10 10.5 L15 6.5" fill="none" stroke="var(--brand-blue)" stroke-width="1"/>
        </svg>
        dean@kolvat.biz
      </li>
      <li>
        <svg class="contact-icon" viewBox="0 0 20 20" aria-hidden="true">
          <circle cx="10" cy="10" r="10" fill="var(--brand-blue)"/>
          <circle cx="10" cy="10" r="5" fill="none" stroke="#fff" stroke-width="1.4"/>
          <path d="M5 10 H15 M10 5 Q7 10 10 15 M10 5 Q13 10 10 15" fill="none" stroke="#fff" stroke-width="1"/>
        </svg>
        www.kestonfieldworks.com
      </li>
    </ul>

    <div class="social" aria-label="Social profiles">
      <span></span><span></span><span></span>
    </div>
  </section>

</main>
</body>
</html>
```